Stationery Set for Velmora Company

I need to create full stationery design for my company; Business Cards, Envelops, Letter Heads, Calendar.
In the letter head and Envelops... only contact information and website links.
Our company is a Service Management company with different domains of innovative services including Technology Service Management, Education Services, Outsourcing Management, Events Management.
I need a modern and innovative design specially for the business card. I some transparent designs and I like it, but don't limit your innovation to what I mentioned. Sky is limit for your innovation.

Target Market(s)

Middle East & Africa

Industry/Entity Type

Business Management

Colors
34a7d8
0355a3
85acd3
86cae7
cee9f5
cfdeed
e4daeb
f3f1f8
ecf7fb

Requirements
Must have
• Name, Title, Email, Mobile
Nice to have
• We have multiple locations in USA, KSA, EGY, so I need ideas about how to include all contact details maybe QR / Barcode or something else.
• Please see our locations and contact information: www.brightvelmora.example
Should not have
• Too much text

```html
<!DOCTYPE html>
<html lang="en">
<head>
<meta charset="utf-8">
<title>Velmora Company Stationery</title>
<link rel="stylesheet" href="https://fonts.googleapis.com/css2?family=Arimo:wght@400;700&family=Michroma&display=swap">
<style>
:root{
  --stage:#eef0f3;
  --paper:#ffffff;
  --brand-deep:#0355a3;
  --brand-sky:#34a7d8;
  --brand-royal:#2a47b3;
  --ink:#3a3a3a;
  --ink-soft:#6a6a6a;
}
*{box-sizing:border-box;margin:0;padding:0}
html,body{width:1200px;height:937px;overflow:hidden;background:var(--stage)}
body{position:relative;font-family:"Arimo",Arial,sans-serif;color:var(--ink)}
.sheet{position:absolute;background:var(--paper);overflow:hidden;border:1px solid #e1e4e8}
.band{position:absolute;left:0;bottom:0;width:100%;display:block}
.brand{position:absolute;display:flex;align-items:center;gap:4px;font-family:"Arimo",Arial,sans-serif;font-weight:700;color:var(--brand-deep);letter-spacing:.02em;line-height:1}
.brand-dot{display:block;border-radius:50%;background:var(--brand-deep)}
.web{position:absolute;font-family:"Michroma",sans-serif;color:#fff;letter-spacing:.16em;white-space:nowrap}

/* letterhead */
.letterhead{left:185px;top:68px;width:385px;height:544px}
.letterhead .brand{left:18px;top:26px;font-size:17px}
.letterhead .brand-dot{width:9px;height:9px}
.letter-body{position:absolute;left:35px;top:136px;width:300px;font-size:5.2px;line-height:1.5;color:var(--ink-soft)}
.letter-body p{margin-bottom:7px}
.letter-body .strong{color:var(--ink);font-weight:700}
.letter-body .gap{margin-bottom:18px}
.signature{width:22px;height:14px;background:#d9dbe0;margin:4px 0 6px}
.contact-list{position:absolute;list-style:none;font-size:4.6px;line-height:1;color:#fff}
.contact-list li{display:flex;align-items:center;gap:3px;margin-bottom:2.6px}
.contact-list .ico{width:5px;height:5px;border-radius:50%;background:#fff;flex:none}
.letterhead .contact-list{left:255px;top:488px}

/* folder */
.folder{left:636px;top:40px;width:458px;height:576px}
.folder .brand{left:160px;top:250px;font-size:34px;gap:8px}
.folder .brand-dot{width:16px;height:16px}
.folder .web{right:26px;bottom:11px;font-size:10px}

/* cards */
.card{width:175px;height:100px}
.card-front{left:46px;top:658px}
.card-back{left:46px;top:785px;height:99px}
.card .brand{left:8px;top:10px;font-size:12px;gap:3px}
.card .brand-dot{width:6px;height:6px}
.card-person{position:absolute;left:8px;top:56px;font-size:6px;line-height:1.25;color:var(--ink)}
.card-person .role{font-size:4px;color:var(--ink-soft)}
.card .contact-list{left:98px;top:68px;font-size:3.3px}
.card .contact-list li{gap:2px;margin-bottom:1.8px}
.card .contact-list .ico{width:3.5px;height:3.5px}

/* envelopes */
.envelope-front{left:265px;top:672px;width:432px;height:209px}
.envelope-front .brand{left:16px;top:26px;font-size:17px}
.envelope-front .brand-dot{width:9px;height:9px}
.envelope-front .web{right:22px;bottom:10px;font-size:8px}
.envelope-back{left:737px;top:672px;width:431px;height:207px}
.flap{position:absolute;left:0;top:0;width:100%;height:72px;border-radius:0 0 46px 46px;background:linear-gradient(90deg,var(--brand-royal),#1f7bd8 55%,var(--brand-royal))}
.flap .web{left:0;right:0;top:29px;text-align:center;font-size:10px}
</style>
</head>
<body>

<svg width="0" height="0" style="position:absolute" aria-hidden="true">
  <defs>
    <linearGradient id="blueBand" x1="0" y1="0" x2="1" y2="0">
      <stop offset="0" stop-color="#2a3fa8"/>
      <stop offset=".55" stop-color="#1f74d3"/>
      <stop offset="1" stop-color="#2a56be"/>
    </linearGradient>
    <symbol id="curveBand" viewBox="0 0 400 200" preserveAspectRatio="none">
      <path d="M0,175 C140,150 280,100 400,20 L400,200 L0,200Z" fill="url(#blueBand)"/>
    </symbol>
  </defs>
</svg>

<!-- Letterhead -->
<section class="sheet letterhead">
  <div class="brand"><span class="brand-dot"></span>Velmora</div>
  <div class="letter-body">
    <p>July 2, 2012</p>
    <p><span class="strong">Dear Client,</span><br>ABC Building, def St., Country Name</p>
    <p>We are pleased to share an update on the services we provide across our offices. Our teams support technology service management, education programmes, outsourcing and events for clients throughout the region. Each engagement is planned with care, delivered on schedule and reviewed with you at every stage so that results stay clear, measurable and aligned with your goals for the year ahead.</p>
    <p class="gap">Our staff will contact you shortly to confirm the next meeting date and agenda.</p>
    <p>Thank you for your continued trust in our work. We look forward to building on this partnership through new projects, shared training sessions and regular reviews. Please reach out to our team with any questions about scope, timing or budget, and we will respond within one working day with the details you need.</p>
    <p>Best Regards,</p>
    <div class="signature" role="img" aria-label="Handwritten signature"></div>
    <p><span class="strong">Dana Reyes</span><br>Director<br><br>ABC Building, def St., Country Name</p>
  </div>
  <svg class="band" height="215" role="img" aria-label="Curved blue wave decoration"><use href="#curveBand"/></svg>
  <ul class="contact-list">
    <li><span class="ico"></span>012 555 0147</li>
    <li><span class="ico"></span>012 555 0192</li>
    <li><span class="ico"></span>info@brightvelmora.example</li>
    <li><span class="ico"></span>www.brightvelmora.example</li>
    <li><span class="ico"></span>Suite 12, Harbor Road, Lakeview</li>
  </ul>
</section>

<!-- Folder -->
<section class="sheet folder">
  <div class="brand"><span class="brand-dot"></span>Velmora</div>
  <svg class="band" height="258" role="img" aria-label="Curved blue wave decoration"><use href="#curveBand"/></svg>
  <div class="web">www.brightvelmora.example</div>
</section>

<!-- Business card front -->
<section class="sheet card card-front">
  <div class="brand"><span class="brand-dot"></span>Velmora</div>
  <svg class="band" height="90" role="img" aria-label="Curved blue wave decoration"><use href="#curveBand"/></svg>
  <div class="card-person">OMAR HADLEY<br><span class="role">Managing Director</span></div>
  <ul class="contact-list">
    <li><span class="ico"></span>012 555 0147</li>
    <li><span class="ico"></span>012 555 0192</li>
    <li><span class="ico"></span>omar@brightvelmora.example</li>
    <li><span class="ico"></span>www.brightvelmora.example</li>
    <li><span class="ico"></span>Suite 12, Harbor Road</li>
  </ul>
</section>

<!-- Business card back -->
<section class="sheet card card-back">
  <div class="brand"><span class="brand-dot"></span>Velmora</div>
  <svg class="band" height="80" role="img" aria-label="Curved blue wave decoration"><use href="#curveBand"/></svg>
</section>

<!-- Envelope front -->
<section class="sheet envelope-front">
  <div class="brand"><span class="brand-dot"></span>Velmora</div>
  <svg class="band" height="200" role="img" aria-label="Curved blue wave decoration"><use href="#curveBand"/></svg>
  <div class="web">www.brightvelmora.example</div>
</section>

<!-- Envelope back -->
<section class="sheet envelope-back">
  <div class="flap"><div class="web">www.brightvelmora.example</div></div>
</section>

</body>
</html>
```